Business Card Design Project

Business Card
We are rebranding with a new logo
Industry/Entity Type
Business
Contact Information for Business Card
Dennis Morvale +61 487215963 dennis@quorv.com.au P.O. Box 872 Fernlow QLD 4309
Requirements
Must have
- Logo

```html
<!DOCTYPE html>
<html lang="en">
<head>
<meta charset="utf-8">
<title>Quorv International – Business Card</title>
<link href="https://fonts.googleapis.com/css2?family=Roboto:wght@400;500&family=Roboto+Condensed:wght@700&display=swap" rel="stylesheet">
<style>
  :root {
    --backdrop: #262626;
    --card: #f1f1f1;
    --brand-blue: #0e8cc4;
    --deep-blue: #0a5a80;
    --light-blue: #1aa6dc;
    --text-grey: #4a4a4a;
  }
  html, body {
    margin: 0;
    width: 1200px;
    height: 960px;
    overflow: hidden;
    background: var(--backdrop);
  }
  .card {
    position: absolute;
    left: 407px;
    top: 143px;
    width: 386px;
    height: 674px;
    border-radius: 18px;
    background: var(--card);
    overflow: hidden;
    font-family: "Roboto", sans-serif;
  }
  .corner-band {
    position: absolute;
    left: 0;
    top: 0;
    width: 386px;
    height: 310px;
  }
  .brand-name {
    position: absolute;
    right: 48px;
    top: 318px;
    margin: 0;
    text-align: right;
    font-family: "Roboto", sans-serif;
    font-weight: 500;
    font-size: 30px;
    line-height: 1.15;
    color: var(--brand-blue);
  }
  .holder-name {
    position: absolute;
    right: 48px;
    top: 480px;
    margin: 0;
    font-family: "Roboto Condensed", sans-serif;
    font-weight: 700;
    font-size: 26px;
    letter-spacing: 0.2px;
    color: var(--brand-blue);
    text-transform: uppercase;
  }
  .contact-list {
    position: absolute;
    right: 48px;
    top: 533px;
    margin: 0;
    padding: 0;
    list-style: none;
    font-size: 16px;
    color: var(--text-grey);
  }
  .contact-item {
    display: flex;
    justify-content: flex-end;
    align-items: center;
    gap: 10px;
    height: 21.5px;
  }
  .contact-item.address { margin-top: 5px; }
  .contact-icon {
    width: 14px;
    height: 14px;
    fill: var(--brand-blue);
    flex: none;
  }
</style>
</head>
<body>
  <div class="card">
    <svg class="corner-band" viewBox="0 0 386 310" aria-hidden="true">
      <defs>
        <linearGradient id="bandFill" x1="0" y1="0" x2="1" y2="0.6">
          <stop offset="0" stop-color="#0a4f72"/>
          <stop offset="0.55" stop-color="#0a78a8"/>
          <stop offset="1" stop-color="#16a0d6"/>
        </linearGradient>
      </defs>
      <path d="M0 0 H386 V4 C250 30 90 150 0 298 Z" fill="var(--light-blue)"/>
      <path d="M0 0 H370 C240 30 80 150 0 292 Z" fill="url(#bandFill)"/>
    </svg>

    <p class="brand-name">Quorv<br>International</p>

    <h1 class="holder-name">Dennis Morvale</h1>

    <ul class="contact-list">
      <li class="contact-item">+61 487215963
        <svg class="contact-icon" viewBox="0 0 24 24"><path d="M6.6 10.8a15.1 15.1 0 0 0 6.6 6.6l2.2-2.2a1 1 0 0 1 1-.25 11.4 11.4 0 0 0 3.6.57 1 1 0 0 1 1 1V20a1 1 0 0 1-1 1A17 17 0 0 1 3 4a1 1 0 0 1 1-1h3.5a1 1 0 0 1 1 1c0 1.25.2 2.45.57 3.57a1 1 0 0 1-.25 1z"/></svg>
      </li>
      <li class="contact-item">dennis@quorv.com.au
        <svg class="contact-icon" viewBox="0 0 24 24"><path d="M2 5h20v14H2z M3 6l9 7 9-7" fill="var(--brand-blue)"/><path d="M3 6.5l9 6.5 9-6.5" fill="none" stroke="#f1f1f1" stroke-width="1.6"/></svg>
      </li>
      <li class="contact-item">www.quorv.com.au
        <svg class="contact-icon" viewBox="0 0 24 24"><circle cx="12" cy="12" r="10"/><path d="M8 7c2 1 3 3 1 5s0 4 2 5M15 5c-1 2 1 3 3 3" fill="none" stroke="#f1f1f1" stroke-width="1.6"/></svg>
      </li>
      <li class="contact-item address">P.O. Box 872, Fernlow QLD 4309
        <svg class="contact-icon" viewBox="0 0 24 24" style="height:18px"><path d="M12 1a8 8 0 0 0-8 8c0 6 8 14 8 14s8-8 8-14a8 8 0 0 0-8-8zm0 11a3 3 0 1 1 0-6 3 3 0 0 1 0 6z"/></svg>
      </li>
    </ul>
  </div>
</body>
</html>
```